Bramblewood Card Company Business Cards

We are a trading card store with Glimmorax, sports and other TCG cards, we need a business card design that encompasses a clean cut, modern style with a retro flare. website is bramblewoodcardco.com for reference. Can utilize a comic book era feel or a more modern outdoor feel to utilize the "Pacific Northwest" elements of tress, mountains, etc.

Industry/Entity Type

Trading cards and collectibles

Contact Information for Business Card

business name, email address, phone number, name, owner job title

Font styles to use
Sans Serif

```html
<!DOCTYPE html>
<html lang="en">
<head>
<meta charset="utf-8">
<title>Bramblewood Card Company – Business Cards</title>
<link href="https://fonts.googleapis.com/css2?family=Montserrat:wght@400;600;800&family=Open+Sans:wght@400;600&display=swap" rel="stylesheet">
<style>
  :root {
    --sky: #1fbde0;
    --sky-light: #3fcbe9;
    --slate: #6b6b6d;
    --slate-dark: #555557;
    --paper: #ffffff;
    --ink: #4a4a4c;
    --backdrop: #2a2c30;
  }
  * { box-sizing: border-box; margin: 0; padding: 0; }
  html, body { width: 1200px; height: 900px; overflow: hidden; }
  body {
    background: var(--backdrop);
    font-family: "Open Sans", sans-serif;
    position: relative;
  }
  .card {
    position: absolute;
    top: 295px;
    width: 540px;
    height: 310px;
    overflow: hidden;
  }
  .card--front { left: 40px; background: var(--paper); }
  .card--back { left: 620px; background: var(--sky); }

  /* front */
  .name-band {
    position: absolute; left: 0; top: 42px;
    width: 262px; height: 104px;
    background: var(--slate);
    padding: 22px 0 0 30px;
  }
  .name-band__name {
    font-family: "Montserrat", sans-serif;
    font-weight: 600;
    font-size: 24px;
    letter-spacing: 1px;
    color: var(--sky);
    text-transform: uppercase;
    white-space: nowrap;
  }
  .name-band__title {
    font-size: 14px;
    color: #e3e3e3;
    margin-top: 2px;
  }
  .brand {
    position: absolute; left: 290px; top: 28px;
    width: 230px; height: 104px;
    display: flex; align-items: center; gap: 10px;
  }
  .brand__mark {
    flex: none; width: 22px; height: 22px;
    border-radius: 50%; background: var(--slate);
  }
  .brand__name {
    font-family: "Montserrat", sans-serif;
    font-weight: 800;
    font-size: 19px;
    line-height: 1.15;
    color: var(--slate-dark);
    text-transform: uppercase;
  }
  .contact-band {
    position: absolute; left: 262px; top: 160px;
    width: 278px; height: 100px;
    background: var(--sky);
    padding: 14px 0 0 20px;
    list-style: none;
  }
  .contact-band li {
    display: flex; align-items: center; gap: 8px;
    color: var(--paper);
    font-size: 14.5px;
    line-height: 24px;
    white-space: nowrap;
  }
  .contact-band svg { width: 12px; height: 12px; flex: none; }
  .address {
    position: absolute; left: 30px; bottom: 32px;
    font-size: 14px;
    color: var(--ink);
    white-space: nowrap;
  }

  /* back */
  .backdrop-art {
    position: absolute; left: 120px; top: 40px;
    width: 300px; height: 250px;
    background: linear-gradient(180deg, var(--sky-light), var(--sky));
    opacity: 0.6;
  }
  .back-brand {
    position: absolute; inset: 0;
    display: flex; align-items: center; justify-content: center; gap: 14px;
  }
  .back-brand__mark {
    width: 30px; height: 30px; border-radius: 50%;
    background: var(--slate);
  }
  .back-brand__name {
    font-family: "Montserrat", sans-serif;
    font-weight: 800;
    font-size: 28px;
    line-height: 1.15;
    color: var(--slate-dark);
    text-transform: uppercase;
  }
</style>
</head>
<body>
  <section class="card card--front">
    <div class="name-band">
      <p class="name-band__name">Dorian Vale</p>
      <p class="name-band__title">CEO/Founder</p>
    </div>
    <div class="brand">
      <span class="brand__mark"></span>
      <p class="brand__name">Bramblewood<br>Card Company</p>
    </div>
    <ul class="contact-band">
      <li>
        <svg viewBox="0 0 12 12"><path d="M2.5 1h2l1 2.5-1.3 1a6 6 0 0 0 3.3 3.3l1-1.3L11 7.5v2A1.5 1.5 0 0 1 9.5 11 8.5 8.5 0 0 1 1 2.5 1.5 1.5 0 0 1 2.5 1z" fill="#fff"/></svg>
        (555) 218 4630
      </li>
      <li>
        <svg viewBox="0 0 12 12"><rect x="0.5" y="2" width="11" height="8" fill="#fff"/><path d="M0.5 2 6 6.5 11.5 2" fill="none" stroke="#1fbde0" stroke-width="1"/></svg>
        info@bramblewoodcardco.com
      </li>
      <li>
        <svg viewBox="0 0 12 12"><circle cx="6" cy="6" r="5.2" fill="none" stroke="#fff" stroke-width="1.2"/><ellipse cx="6" cy="6" rx="2.2" ry="5.2" fill="none" stroke="#fff" stroke-width="1"/><path d="M1 6h10" stroke="#fff" stroke-width="1"/></svg>
        www.bramblewoodcardco.com
      </li>
    </ul>
    <p class="address">P.O. Box 3817 Cedar Row Harlow Vale BC 6210</p>
  </section>

  <section class="card card--back">
    <div class="backdrop-art" role="img" aria-label="Faint mountain range illustration"></div>
    <div class="back-brand">
      <span class="back-brand__mark"></span>
      <p class="back-brand__name">Bramblewood<br>Card Company</p>
    </div>
  </section>
</body>
</html>
```